Web Design Project

Due to client commitments, we don't have time in-house to complete this project...
We need a design refresh for our web company! It's time for us to move things along, so we're looking to SketchBazaar to get this done!
Our clients tend to be associations and government, with some element of business clients. We need a design that appeals to this sophisticated target market.
Our current web site can be found at www.tallowbrookweb.ca. We are looking for a more personable, contemporary look for the new site design. However, you can see our logo on this site, and some of the content.
The design you provide will be implemented in Tessera. The design winner will only need to provide the PSD or Fireworks PNG format. We anticipate creating the template coding in-house.
However, if you have experience creating Tessera templates, please let us know as we may ask you to bid separately to do that phase of the project.
We've provided you with wireframes of the home page and the inside page, along with Adobe Illustrator and PSD versions of our logo.
For the home page, we've indicated that we'd like to have a slider implemented into the design. For the purpose of design, we believe we'll use this slider: http://demo.vorntiplugins.com/zesty-panelle-slider.html.
The slider will contain inspiration photos related to each of the tabs. Ideally, we would like you to suggest the images for the slider. The dimension of the slider can be adjusted. We would like more space for the image with less for the text. The slider height should be sufficient to ensure the image "stimulates" the audience and sets the tone for the landing page.
The wireframe is provided to illustrate the placement of content and menu items. The exact dimensions of each component can be revised as you see fit.
Target Market(s)
Our clients tend to be associations, non-profit, government, and business clients. We need a design that appeals to this sophisticated target market.
Industry/Entity Type
Business
Look and feel

```html
<!DOCTYPE html>
<html lang="en">
<head>
<meta charset="utf-8">
<title>TallowBrook Communications</title>
<link href="https://fonts.googleapis.com/css2?family=Arimo:wght@400;700&display=swap" rel="stylesheet">
<style>
:root{
  --red:#c8141c;
  --red-dark:#a80f16;
  --orange:#f29a1c;
  --ink:#222;
  --text:#444;
  --muted:#888;
  --dark:#2e2e2e;
  --panel:#3b3b3b;
  --line:#dcdcdc;
  --page:#ffffff;
  --canvas:#e8e8e8;
  --soft:#f3f3f3;
}
*{box-sizing:border-box;margin:0;padding:0}
html,body{width:878px;height:1200px;overflow:hidden}
body{background:var(--canvas);font-family:"Arimo",Arial,sans-serif;color:var(--text);font-size:11px;position:relative}
.topbar{position:absolute;left:0;top:0;width:878px;height:24px;background:var(--dark);color:#ccc;font-size:9.5px;display:flex;align-items:center;justify-content:space-between;padding:0 30px}
.topbar .contact span{margin-left:14px}
.topbar .phone,.topbar .mail{color:#fff;background:var(--red);padding:2px 6px}
.page{position:absolute;left:22px;top:24px;width:834px;height:1176px;background:var(--page);box-shadow:0 0 6px rgba(0,0,0,.12)}
.header{position:absolute;left:8px;top:0;width:818px;height:100px}
.brand{position:absolute;left:0;top:18px;display:flex;align-items:center;gap:10px}
.brand .mark{width:44px;height:44px;border-radius:50%;background:var(--red)}
.brand .name{font-size:24px;font-weight:700;color:var(--ink);line-height:1}
.quote{position:absolute;right:0;top:12px;width:118px;height:26px;background:var(--orange);color:#fff;font-size:12px;display:flex;align-items:center;justify-content:center}
.social{position:absolute;right:0;top:56px;display:flex;gap:6px}
.social span{width:20px;height:20px;background:#3d87c9;border-radius:3px}
.social span+span{background:#35518f}
.nav{position:absolute;left:8px;top:102px;width:818px;height:30px;border-bottom:3px solid var(--red);display:flex}
.nav a{flex:1;display:flex;align-items:center;justify-content:center;color:var(--ink);text-decoration:none;font-size:10.5px;border-right:1px solid var(--line)}
.nav a:last-child{border-right:0}
.nav a.active{color:var(--red);font-weight:700}
.slider{position:absolute;left:8px;top:144px;width:818px;height:310px;display:flex}
.slide-photo{width:570px;height:100%;background:linear-gradient(120deg,#c7ccd2,#8a8f96 45%,#3d3a38)}
.slide-panel{flex:1;background:var(--panel);color:#ddd;display:flex;flex-direction:column}
.slide-panel h2{background:#262626;color:#fff;font-size:12px;padding:9px 14px;font-weight:700}
.slide-panel p{padding:12px 14px 0;font-size:10.5px;line-height:1.45}
.slide-panel .more{padding:6px 14px;text-align:right;color:var(--red);font-size:10px}
.slide-tabs{margin-top:auto}
.slide-tabs div{background:var(--red);color:#fff;font-size:11.5px;padding:11px 14px;border-top:2px solid var(--red-dark)}
.services{position:absolute;left:8px;top:470px;width:818px;height:152px;display:flex;gap:7px}
.tile{flex:1;display:flex;flex-direction:column}
.tile .shot{flex:1}
.tile .label{height:24px;background:var(--red);color:#fff;font-size:10.5px;display:flex;align-items:center;justify-content:center}
.shot.web{background:linear-gradient(135deg,#555,#1d1d1d)}
.shot.apps{background:linear-gradient(135deg,#7db7e4,#d4484c)}
.shot.soft{background:linear-gradient(135deg,#e9eef3,#9aaabb)}
.shot.pdf{background:linear-gradient(135deg,#f2f2f2,#c9252b)}
.shot.cms{background:linear-gradient(135deg,#f4f6f7,#5aa4d6)}
.columns{position:absolute;left:8px;top:644px;width:818px;height:300px;display:flex;gap:18px}
.column{flex:1;border:1px solid var(--line)}
.column h3{background:var(--soft);border-bottom:2px solid var(--red);height:26px;font-size:11px;font-weight:700}
.column h3 span{display:inline-block;height:26px;line-height:26px;padding:0 18px;background:var(--red);color:#fff}
.entry{display:flex;gap:10px;padding:12px 10px;border-bottom:1px solid #eee;height:90px}
.entry:last-child{border-bottom:0}
.thumb{width:50px;height:50px;flex:none;background:linear-gradient(135deg,#d9dde2,#8e959d)}
.thumb.wide{width:78px;height:56px;background:linear-gradient(135deg,#eef1f4,#9fb0c2)}
.entry .date{color:var(--muted);font-size:9px;margin-bottom:3px}
.entry .title{color:var(--ink);font-weight:700;font-size:10px;margin-bottom:3px}
.entry p{font-size:9.5px;line-height:1.35}
.entry .more{color:var(--red);font-size:9px;text-align:right}
.footer-cols{position:absolute;left:8px;top:962px;width:818px;height:156px;display:flex;gap:10px}
.fcol{flex:1;border:1px solid var(--line);border-top:3px solid var(--red)}
.fcol h4{background:var(--soft);color:var(--red);font-size:11px;font-weight:400;padding:7px 10px}
.fcol ul{list-style:none;padding:6px 0 0 26px}
.fcol li{font-size:9.5px;line-height:20px;position:relative}
.fcol li::before{content:"";position:absolute;left:-12px;top:8px;width:4px;height:4px;background:var(--red)}
.sitemap{position:absolute;left:0;top:1138px;width:834px;text-align:center;font-size:10px;color:var(--ink)}
.baseline{position:absolute;left:0;bottom:0;width:834px;height:6px;background:var(--red)}
</style>
</head>
<body>
<div class="topbar">
  <div class="links">www.tallowbrookhosting.ca &nbsp;|&nbsp; www.tallowbrookdesign.ca</div>
  <div class="contact"><span>Contact us today</span><span class="phone">613-555-0148</span><span class="mail">sales@tallowbrookweb.ca</span></div>
</div>
<div class="page">
  <header class="header">
    <div class="brand"><span class="mark"></span><span class="name">TallowBrook</span></div>
    <div class="quote">Request a Quote</div>
    <div class="social" aria-label="Social links"><span></span><span></span></div>
  </header>
  <nav class="nav">
    <a class="active">Home</a><a>Web Design</a><a>Mobile Apps</a><a>Custom Software</a><a>Custom Service</a><a>Accessible PDF/HTML</a><a>Contact Us</a>
  </nav>
  <section class="slider">
    <div class="slide-photo" role="img" aria-label="Team of professionals gathered around a laptop in an office"></div>
    <div class="slide-panel">
      <h2>Our Vision</h2>
      <p>We partner with associations, government and business to build accessible, thoughtful websites that grow with your mission and your audience over time.</p>
      <div class="more">read more</div>
      <div class="slide-tabs"><div>Business</div><div>Government</div><div>Associations/Non-profit</div></div>
    </div>
  </section>
  <section class="services">
    <div class="tile"><div class="shot web" role="img" aria-label="Web design concept image"></div><div class="label">Web Design</div></div>
    <div class="tile"><div class="shot apps" role="img" aria-label="Smartphone with app icons"></div><div class="label">Mobile Apps</div></div>
    <div class="tile"><div class="shot soft" role="img" aria-label="Software box illustration"></div><div class="label">Custom Software</div></div>
    <div class="tile"><div class="shot pdf" role="img" aria-label="Document file illustration"></div><div class="label">Accessible PDF / HTML</div></div>
    <div class="tile"><div class="shot cms" role="img" aria-label="Content management platform illustration"></div><div class="label">CMS : Tessera / Vellum</div></div>
  </section>
  <section class="columns">
    <div class="column">
      <h3><span>Blog archive</span></h3>
      <div class="entry"><div class="thumb" role="img" aria-label="Author photo"></div><div><div class="date">2 days ago</div><p>Our team shared fresh thinking on accessible design, clean layouts and content that helps members find what they need faster online.</p><div class="more">read more</div></div></div>
      <div class="entry"><div class="thumb" role="img" aria-label="Author photo"></div><div><div class="date">2 days ago</div><p>Our team shared fresh thinking on accessible design, clean layouts and content that helps members find what they need faster online.</p><div class="more">read more</div></div></div>
      <div class="entry"><div class="thumb" role="img" aria-label="Author photo"></div><div><div class="date">2 days ago</div><p>Our team shared fresh thinking on accessible design, clean layouts and content that helps members find what they need faster online.</p><div class="more">read more</div></div></div>
    </div>
    <div class="column">
      <h3><span>Featured Projects</span></h3>
      <div class="entry"><div class="thumb wide" role="img" aria-label="Project screenshot"></div><div><div class="title">Project description Summary</div><p>A new portal for a regional association, built for clear navigation, accessible forms and easy updates by staff.</p><div class="more">read more</div></div></div>
      <div class="entry"><div class="thumb wide" role="img" aria-label="Project screenshot"></div><div><div class="title">Project description Summary</div><p>A new portal for a regional association, built for clear navigation, accessible forms and easy updates by staff.</p><div class="more">read more</div></div></div>
      <div class="entry"><div class="thumb wide" role="img" aria-label="Project screenshot"></div><div><div class="title">Project description Summary</div><p>A new portal for a regional association, built for clear navigation, accessible forms and easy updates by staff.</p><div class="more">read more</div></div></div>
    </div>
  </section>
  <section class="footer-cols">
    <div class="fcol"><h4>Web Design</h4><ul><li>Item one</li><li>Item two</li><li>Item three</li><li>Item four</li><li>Item five</li></ul></div>
    <div class="fcol"><h4>Mobile Apps</h4><ul><li>Item one</li><li>Item two</li><li>Item three</li><li>Item four</li><li>Item five</li></ul></div>
    <div class="fcol"><h4>Accessible PDF / HTML</h4><ul><li>Item one</li><li>Item two</li><li>Item three</li><li>Item four</li><li>Item five</li></ul></div>
    <div class="fcol"><h4>CMS : Tessera / Vellum</h4><ul><li>Item one</li><li>Item two</li><li>Item three</li><li>Item four</li><li>Item five</li></ul></div>
  </section>
  <div class="sitemap">Site Map | Home | Web Design | Mobile Apps | Accessible PDF/HTML | CMS: Tessera/Vellum</div>
  <div class="baseline"></div>
</div>
</body>
</html>
```